Local fast-growing company in the service sector

We are looking for a modern business card design, which should also appear on our letterheads

Target Market(s)

Private and industrial sectors

Contact Information for Business Card

Vorname Name
Kellberger Str. 18
74219 Lindenfeld
Tel.: 07146-839214-0
Name@agentur-kvtl.de

Colors
9d9d9d
919191
aaaaaa

Requirements
Must have
• The logo (file) in silver

```html
<!DOCTYPE html>
<html lang="de">
<head>
<meta charset="utf-8">
<title>KVTL Visitenkarte</title>
<link href="https://fonts.googleapis.com/css2?family=Exo+2:wght@400;600&display=swap" rel="stylesheet">
<style>
  :root {
    --page-bg: #e9e9e9;
    --card-white: #ffffff;
    --silver: #9d9d9d;
    --silver-mid: #919191;
    --silver-light: #aaaaaa;
    --ink: #2b2b2b;
    --band-dark: #1e1c1d;
    --rule: #c4c4c4;
  }
  * { box-sizing: border-box; margin: 0; padding: 0; }
  html, body {
    width: 1200px; height: 1200px; overflow: hidden;
    background: var(--page-bg);
    font-family: "Exo 2", "Helvetica Neue", sans-serif;
  }
  .canvas {
    width: 1200px; height: 1200px;
    display: flex; align-items: center; justify-content: center;
  }
  .business-card {
    position: relative;
    width: 1000px; height: 620px;
    background: var(--card-white);
    box-shadow: 0 10px 30px rgba(0,0,0,0.18);
    overflow: hidden;
  }
  .brand {
    position: absolute; top: 70px; right: 80px;
    display: flex; align-items: center; gap: 22px;
  }
  .brand-mark {
    width: 110px; height: 110px;
    background: var(--silver-light);
  }
  .brand-text { display: flex; flex-direction: column; }
  .brand-name {
    font-size: 92px; font-weight: 600; line-height: 0.9;
    color: var(--silver); letter-spacing: 2px;
  }
  .brand-web {
    font-size: 28px; font-weight: 600;
    color: var(--silver); letter-spacing: 1px;
    margin-top: 6px;
  }
  .person-name {
    position: absolute; left: 60px; top: 318px;
    font-size: 54px; font-weight: 400; color: var(--ink);
  }
  .divider {
    position: absolute; left: 60px; right: 60px; top: 392px;
    height: 2px; background: var(--rule);
  }
  .contact-list {
    position: absolute; left: 60px; top: 418px;
    list-style: none;
    display: flex; flex-direction: column; gap: 16px;
  }
  .contact-item {
    display: flex; align-items: center; gap: 22px;
    font-size: 32px; color: var(--ink);
  }
  .contact-icon { width: 34px; height: 34px; flex: none; }
  .address {
    position: absolute; right: 70px; top: 422px;
    font-style: normal; font-size: 28px; color: var(--ink);
    text-align: right; line-height: 1.45;
    display: flex; flex-direction: column;
  }
  .address-line { display: flex; align-items: center; justify-content: flex-end; gap: 12px; }
  .pin-icon { width: 22px; height: 30px; flex: none; }
  .bottom-band {
    position: absolute; left: 0; right: 0; bottom: 0; height: 34px;
    display: flex;
  }
  .band-dark { width: 60%; background: var(--band-dark); }
  .band-silver { flex: 1; background: var(--silver-mid); }
</style>
</head>
<body>
<div class="canvas">
  <section class="business-card">
    <div class="brand">
      <div class="brand-mark"></div>
      <div class="brand-text">
        <span class="brand-name">KVTL</span>
        <span class="brand-web">agentur-kvtl.de</span>
      </div>
    </div>

    <h1 class="person-name">Vorname Name</h1>
    <div class="divider"></div>

    <ul class="contact-list">
      <li class="contact-item">
        <svg class="contact-icon" viewBox="0 0 34 34" aria-hidden="true">
          <path d="M3 12 Q17 2 31 12 L27 16 L23 12 L11 12 L7 16 Z" fill="var(--silver)"/>
          <rect x="6" y="17" width="22" height="13" rx="2" fill="var(--silver)"/>
          <circle cx="17" cy="23" r="3.5" fill="#fff"/>
        </svg>
        <span>07146-839214-0</span>
      </li>
      <li class="contact-item">
        <svg class="contact-icon" viewBox="0 0 34 34" aria-hidden="true">
          <rect x="2" y="5" width="30" height="24" fill="var(--silver-light)"/>
        </svg>
        <span>Name@agentur-kvtl.de</span>
      </li>
    </ul>

    <address class="address">
      <span class="address-line">Kellberger Str. 18
        <svg class="pin-icon" viewBox="0 0 22 30" aria-hidden="true">
          <path d="M11 1 C5 1 1 5.5 1 11 C1 18 11 29 11 29 C11 29 21 18 21 11 C21 5.5 17 1 11 1 Z" fill="var(--silver)"/>
          <circle cx="11" cy="11" r="4" fill="#fff"/>
        </svg>
      </span>
      <span class="address-line">74219 Lindenfeld</span>
    </address>

    <div class="bottom-band">
      <div class="band-dark"></div>
      <div class="band-silver"></div>
    </div>
  </section>
</div>
</body>
</html>
```